Upmarket Dessert Lounge needs a Business Card Design

We are an upmarket dessert lounge needing a business card to match our image.

We want something that is simple yet beautiful, feminine, classy, sophisticated and elegant. We want it to stand out and don't mind if it is bold.

The design should include our logo and colours of red or maroon with gold highlights. We don't mind if black is used.

Marlow & Quince

Target Market(s)

For those who like to indulge or treat themselves and give in to their temptations on good quality desserts.

Industry/Entity Type

Business

Requirements
Must have
• Must include our logo and our name

Marlow & Quince

M & Q

```html
<!DOCTYPE html>
<html lang="en">
<head>
<meta charset="utf-8">
<title>Marlow &amp; Quince — Business Card</title>
<link rel="stylesheet" href="https://fonts.googleapis.com/css2?family=PT+Sans:wght@400;700&display=swap">
<style>
  :root {
    --backdrop: #5a3421;
    --card: #2a2526;
    --card-edge: #3a3334;
    --gold: #f3d6a0;
    --gold-soft: #e9c98f;
  }
  * { margin: 0; padding: 0; box-sizing: border-box; }
  html, body {
    width: 1200px;
    height: 402px;
    overflow: hidden;
  }
  body {
    background: var(--backdrop);
    font-family: "PT Sans", "Myriad Pro", Arial, sans-serif;
    color: var(--gold);
    position: relative;
  }
  .card {
    position: absolute;
    top: 56px;
    width: 511px;
    height: 290px;
    background: var(--card);
    border-radius: 18px;
    box-shadow: 0 0 0 1px var(--card-edge), 0 4px 10px rgba(0,0,0,0.35);
  }
  .card--front { left: 71px; }
  .card--back { left: 624px; }

  .brand-name {
    position: absolute;
    left: 30px;
    top: 116px;
    width: 244px;
    text-align: center;
    font-size: 24px;
    font-weight: 400;
    letter-spacing: 0.5px;
    color: var(--gold);
  }

  .contact {
    position: absolute;
    left: 329px;
    top: 70px;
    width: 155px;
  }
  .contact__name {
    font-size: 15px;
    font-weight: 700;
    line-height: 18px;
  }
  .contact__title {
    font-size: 12px;
    font-weight: 400;
  }
  .rule {
    height: 1px;
    background: var(--gold-soft);
  }
  .contact .rule { margin: 10px 0 10px; }
  .contact__list {
    list-style: none;
    font-size: 12.5px;
    line-height: 17px;
  }
  .contact__list li {
    display: flex;
    align-items: center;
    gap: 4px;
  }
  .contact__list svg { width: 9px; height: 10px; fill: var(--gold); flex: none; }
  .contact__address {
    font-size: 12.5px;
    line-height: 15px;
    font-style: normal;
  }

  .website {
    position: absolute;
    left: 34px;
    top: 252px;
    font-size: 16px;
  }
  .website-rule {
    position: absolute;
    left: 231px;
    top: 268px;
    width: 263px;
  }

  .monogram {
    position: absolute;
    inset: 0;
    display: flex;
    align-items: center;
    justify-content: center;
    font-size: 72px;
    font-weight: 400;
    letter-spacing: 2px;
    color: var(--gold);
  }
</style>
</head>
<body>
  <section class="card card--front" aria-label="Business card front">
    <p class="brand-name">Marlow &amp; Quince</p>

    <div class="contact">
      <p class="contact__name">Your name, <span class="contact__title">Title</span></p>
      <div class="rule"></div>
      <ul class="contact__list">
        <li>
          <svg viewBox="0 0 10 10" aria-hidden="true"><path d="M2 0.5 L3.6 2.6 L2.7 3.6 Q3.8 6 6.3 7.3 L7.4 6.4 L9.5 8 L8.3 9.5 Q2.5 8.5 0.5 1.7 Z"/></svg>
          987-654-3210
        </li>
        <li>
          <svg viewBox="0 0 10 10" aria-hidden="true"><path d="M2.5 0 H7.5 V10 H2.5 Z M3.4 1.2 V6 H6.6 V1.2 Z"/></svg>
          987-654-3210
        </li>
        <li>
          <svg viewBox="0 0 10 10" aria-hidden="true"><path d="M0.5 2.5 H9.5 V8 H0.5 Z M1 2.8 L5 5.6 L9 2.8" /><path d="M0.8 2.8 L5 5.8 L9.2 2.8" stroke="#2a2526" stroke-width="0.9" fill="none"/></svg>
          info@marlowquince.com
        </li>
      </ul>
      <div class="rule"></div>
      <address class="contact__address">Street Name, City Name<br>State Zip Code</address>
    </div>

    <p class="website">www.marlowquince.com</p>
    <div class="rule website-rule"></div>
  </section>

  <section class="card card--back" aria-label="Business card back">
    <p class="monogram">M &amp; Q</p>
  </section>
</body>
</html>
```